Join Wait / Reservations Handout

This is a handout for guests with information about the ability to join our
waitlist and/or make reservations. It will be handed out to any guest that ends up waiting on our waitlist to be seated. It will describe how our waitlist and reservations system works. It is informational for them to download our mobile app.

It was forcing me to move the look and feel sliders. Please refer to our branding guide for look and feel.

Industry/Entity Type

Hospitality

Contact Information for Business Card

One of the attached documents give a very generic layout of the information we need on this card. This layout is more for where we wanted the information placed and has nothing to do with the design aspects of the piece. Please use your imagination. Any of the 5 colors in the branding guide can be used anywhere. The pineapple design can be used anywhere in any color combination.

If you require any other files please let me know. Thanks

Other font styles liked:
• Please see attached branding guide

Requirements
Must have
• The only color requirement is that the logo be the blue with teal lettering...This has to match our app store logo.

```html
<!DOCTYPE html>
<html lang="en">
<head>
<meta charset="utf-8">
<title>Join the Wait / Reservations Handout</title>
<link rel="stylesheet" href="https://fonts.googleapis.com/css2?family=Jost:ital,wght@0,400;0,500;1,400&display=swap">
<style>
  :root {
    --navy: #063349;
    --teal: #67aeb3;
    --pink: #f7b5ac;
    --gold: #e5b03d;
    --backdrop: #bdbdbf;
  }
  * { margin: 0; padding: 0; box-sizing: border-box; }
  html, body {
    width: 1146px;
    height: 1200px;
    overflow: hidden;
    background: var(--backdrop);
    font-family: "Jost", "Futura", sans-serif;
  }
  .canvas { position: relative; width: 1146px; height: 1200px; }

  .card {
    position: absolute;
    top: 237px;
    width: 422px;
    height: 737px;
    background: var(--navy);
    overflow: hidden;
  }
  .card--front { left: 118px; }
  .card--back { left: 588px; }

  .line {
    position: absolute;
    left: 0;
    width: 100%;
    text-align: center;
    transform: translateY(-50%);
    white-space: nowrap;
    line-height: 1.1;
  }

  /* Front */
  .front-heading { color: var(--teal); font-size: 32px; font-weight: 400; letter-spacing: 0.5px; }
  .brand-name { color: var(--teal); font-size: 38px; font-weight: 500; letter-spacing: 3px; }
  .search-label { color: var(--teal); font-size: 32px; font-weight: 400; }
  .search-term { color: var(--teal); font-size: 27px; font-style: italic; letter-spacing: 0.3px; }

  /* Back bands */
  .band { position: absolute; left: 0; width: 100%; }
  .band--wait { top: 0; height: 169px; background: var(--navy); color: var(--teal); }
  .band--reserve { top: 169px; height: 198px; background: var(--teal); color: var(--navy); }
  .band--buffet { top: 367px; height: 194px; background: var(--pink); color: var(--navy); }
  .band--groups { top: 561px; height: 176px; background: var(--gold); color: var(--navy); }

  .band-title { font-size: 34px; font-weight: 400; }
  .band-title--strong { font-size: 35px; font-weight: 500; }
  .band-note { font-size: 22px; font-weight: 400; }
  .band-plus { font-size: 30px; }
</style>
</head>
<body>
<main class="canvas">

  <section class="card card--front" aria-label="Front of handout">
    <p class="line front-heading" style="top:101px">SAVE THE WAIT...</p>
    <p class="line front-heading" style="top:165px">DOWNLOAD OUR APP</p>
    <p class="line brand-name" style="top:379px">HARBOR TABLE</p>
    <p class="line search-label" style="top:581px">SEARCH</p>
    <p class="line search-term" style="top:635px">“HARBOR TABLE EASTFIELD”</p>
  </section>

  <section class="card card--back" aria-label="Back of handout">
    <div class="band band--wait">
      <p class="line band-title" style="top:59px">When to Join the Wait?</p>
      <p class="line band-title" style="top:109px">Anytime</p>
    </div>
    <div class="band band--reserve">
      <p class="line band-title band-title--strong" style="top:62px">When to Reserve?</p>
      <p class="line band-note" style="top:115px">Anytime, 2 hours in advance</p>
      <p class="line band-note" style="top:143px">(Excluding weekends, open-2pm)</p>
    </div>
    <div class="band band--buffet">
      <p class="line band-title band-title--strong" style="top:42px">Sunday</p>
      <p class="line band-plus" style="top:82px">+</p>
      <p class="line band-title band-title--strong" style="top:126px">Holiday Buffets</p>
      <p class="line band-note" style="top:158px">(Coming June 2018)</p>
    </div>
    <div class="band band--groups">
      <p class="line band-note" style="top:74px">Large Groups handled/contacted</p>
      <p class="line band-note" style="top:103px">by Catering Manager</p>
    </div>
  </section>

</main>
</body>
</html>
```